Redesign of business card for Cedar Ridge Mechanical

We are looking for a new design for our business cards for Cedar Ridge Mechanical. We are a plumbing & HVAC construction company, operating on the West Coast of Canada and USA. Logo attached.
Industry/Entity Type
Construction - Plumbing & HVAC
Contact Information for Business Card
Name, address, phone numbers, email, website address
Look and feel
Each slider illustrates characteristics of the customer's brand and the style your logo design should communicate.

```html
<!DOCTYPE html>
<html lang="en">
<head>
<meta charset="utf-8">
<title>Cedar Ridge Mechanical – Business Card</title>
<link href="https://fonts.googleapis.com/css2?family=Poppins:wght@300;400;600;700&display=swap" rel="stylesheet">
<style>
  :root {
    --bg: #222222;
    --card-light: #e2e2e2;
    --card-dark: #141414;
    --ink: #111111;
    --ink-soft: #2a2a2a;
    --band: #c4c4c4;
    --dark-text: #2c2c2c;
  }
  * { margin: 0; padding: 0; box-sizing: border-box; }
  html, body { width: 1200px; height: 780px; overflow: hidden; }
  body {
    background: var(--bg);
    font-family: "Poppins", sans-serif;
    display: flex;
    align-items: center;
    justify-content: center;
    gap: 50px;
  }
  .card {
    width: 520px;
    height: 300px;
    border-radius: 22px;
    position: relative;
    overflow: hidden;
  }
  .card-front {
    background: var(--card-light);
    color: var(--ink);
  }
  .shade-band {
    position: absolute;
    left: 0; right: 0;
    top: 78px;
    height: 70px;
    background: radial-gradient(ellipse at center, var(--band) 0%, rgba(196,196,196,0) 70%);
  }
  .front-content {
    position: relative;
    display: flex;
    flex-direction: column;
    align-items: center;
    padding-top: 30px;
    text-align: center;
  }
  .brand {
    display: flex;
    align-items: center;
    gap: 8px;
    font-weight: 600;
    font-size: 17px;
    letter-spacing: 0.5px;
  }
  .brand-mark {
    width: 14px; height: 14px;
    border: 2px solid var(--ink);
    border-radius: 3px;
  }
  .person-name {
    margin-top: 22px;
    font-size: 26px;
    line-height: 1;
  }
  .person-name .first { font-weight: 700; }
  .person-name .last { font-weight: 300; }
  .person-role {
    margin-top: 6px;
    font-size: 12px;
    font-weight: 600;
  }
  .contact-icons {
    margin-top: 14px;
    display: flex;
    gap: 6px;
  }
  .icon {
    width: 16px; height: 16px;
    border-radius: 50%;
    background: var(--ink);
    display: flex; align-items: center; justify-content: center;
  }
  .icon svg { width: 10px; height: 10px; }
  .contact-lines {
    margin-top: 8px;
    font-size: 12px;
    line-height: 1.45;
    color: var(--ink-soft);
  }
  .address-icon { margin-top: 10px; }
  .address {
    margin-top: 4px;
    font-size: 12px;
    color: var(--ink-soft);
  }
  .card-back {
    background: var(--card-dark);
    display: flex;
    align-items: center;
    justify-content: center;
  }
  .back-brand {
    display: flex;
    align-items: center;
    gap: 14px;
    color: var(--dark-text);
    font-weight: 600;
    font-size: 28px;
    letter-spacing: 1px;
  }
  .back-brand .brand-mark {
    width: 24px; height: 24px;
    border: 3px solid var(--dark-text);
    border-radius: 5px;
  }
</style>
</head>
<body>
  <section class="card card-front">
    <div class="shade-band"></div>
    <div class="front-content">
      <div class="brand"><span class="brand-mark"></span>Cedar Ridge Mechanical</div>
      <h1 class="person-name"><span class="first">Marta</span> <span class="last">Kovalenko</span></h1>
      <p class="person-role">Founder &amp; CEO</p>
      <div class="contact-icons">
        <span class="icon" aria-label="Phone">
          <svg viewBox="0 0 10 10"><path d="M2 1 L4 1 L4.5 3 L3.5 4 Q4.5 5.8 6 6.5 L7 5.5 L9 6 L9 8 Q8.5 9 7 9 Q1 8 1 3 Q1 1.5 2 1Z" fill="#fff"/></svg>
        </span>
        <span class="icon" aria-label="Email">
          <svg viewBox="0 0 10 10"><rect x="1" y="2.5" width="8" height="5.5" fill="none" stroke="#fff" stroke-width="1"/><path d="M1 2.5 L5 5.5 L9 2.5" fill="none" stroke="#fff" stroke-width="1"/></svg>
        </span>
        <span class="icon" aria-label="Website">
          <svg viewBox="0 0 10 10"><circle cx="5" cy="5" r="3.8" fill="none" stroke="#fff" stroke-width="1"/><ellipse cx="5" cy="5" rx="1.6" ry="3.8" fill="none" stroke="#fff" stroke-width="0.8"/><line x1="1.2" y1="5" x2="8.8" y2="5" stroke="#fff" stroke-width="0.8"/></svg>
        </span>
      </div>
      <div class="contact-lines">
        <p>07 5120 3344</p>
        <p>www.brightlineworks.com.au</p>
        <p>admin@brightlineworks.com.au</p>
      </div>
      <span class="icon address-icon" aria-label="Address">
        <svg viewBox="0 0 10 10"><path d="M5 9.5 Q1.8 5.8 1.8 4 A3.2 3.2 0 0 1 8.2 4 Q8.2 5.8 5 9.5Z" fill="#fff"/><circle cx="5" cy="4" r="1.1" fill="#111"/></svg>
      </span>
      <p class="address">482 Harbourview Lane, Easton, WI 53120</p>
    </div>
  </section>
  <section class="card card-back">
    <div class="back-brand"><span class="brand-mark"></span>Cedar Ridge Mechanical</div>
  </section>
</body>
</html>
```